Brell Stone Company Business Cards

Front and Back Business Card - logo and text setup - cool design. I need workable photoshop or illustrator files so I can setup each employee card with design that is created
Updates

Hi everyone, thank you for the great entries. Please no more white and blue cards - there are so many already - black and silver only now please. thanks!

Target Market(s)

Construction Industry - Facility Managers

Industry/Entity Type

Construction

Contact Information for Business Card

I really like contemporary simplistic looks - clean neat....not opposed to seeing some black backrounds

Requirements
Must have
• Logo/website address with design on front only - www.brellstone-example.com (logo attached)
• Back:
• Name/Title/Company Address/Phone/email address
Nice to have
• Cool design
Should not have
• Nothing gimmicky like Fire or Water - since we are a Fire Protection company - it has all been done

```html
<!DOCTYPE html>
<html lang="en">
<head>
<meta charset="utf-8">
<title>Brell Stone Company Business Cards</title>
<link rel="stylesheet" href="https://fonts.googleapis.com/css2?family=Lato:wght@400;700;900&display=swap">
<style>
  :root {
    --backdrop: #bfc1c3;
    --card-dark: #1e1e1f;
    --card-silver: #e3e5e7;
    --silver: #c3c7cb;
    --silver-dim: #9ea3a8;
    --black: #1b1b1c;
    --ink-grey: #55585c;
  }
  * { margin: 0; padding: 0; box-sizing: border-box; }
  html, body {
    width: 1200px; height: 1200px; overflow: hidden;
    background: var(--backdrop);
    font-family: "Lato", sans-serif;
  }
  .canvas { position: relative; width: 1200px; height: 1200px; }
  .card {
    position: absolute; left: 250px; width: 708px; height: 404px;
  }
  .card--front { top: 144px; background: var(--card-dark); }
  .card--back { top: 582px; background: var(--card-silver); }

  .wordmark {
    position: absolute; font-weight: 900;
    letter-spacing: -0.5px; white-space: nowrap; line-height: 1;
  }
  .card--front .wordmark {
    left: 0; right: 0; top: 150px; text-align: center; font-size: 64px;
    color: var(--silver);
  }
  .card--front .website {
    position: absolute; left: 0; right: 0; top: 342px;
    text-align: center; color: var(--silver-dim); font-size: 19px;
  }
  .card--back .wordmark { left: 60px; top: 173px; font-size: 47px; color: var(--black); }

  .divider {
    position: absolute; left: 380px; top: 108px; width: 1.5px; height: 188px;
    background: var(--silver-dim);
  }
  .details { position: absolute; left: 408px; top: 104px; color: var(--ink-grey); }
  .details .name { font-size: 21px; font-weight: 700; color: var(--black); line-height: 1.2; }
  .details .title { font-size: 16px; margin-top: 2px; }
  .details .address { font-size: 16px; line-height: 20px; margin-top: 16px; }
  .contact-list { list-style: none; margin-top: 12px; font-size: 16px; }
  .contact-list li { display: flex; align-items: center; height: 21.5px; }
  .contact-list svg { width: 12px; height: 12px; margin-right: 9px; fill: var(--black); flex: none; }
</style>
</head>
<body>
<main class="canvas">
  <section class="card card--front">
    <div class="wordmark">Brell Stone</div>
    <div class="website">www.brellstone-example.com</div>
  </section>

  <section class="card card--back">
    <div class="wordmark">Brell Stone</div>
    <div class="divider"></div>
    <div class="details">
      <div class="name">Dana Whitfield</div>
      <div class="title">Director</div>
      <div class="address">48 Harbor View Lane<br>Millbrook, NY 10599</div>
      <ul class="contact-list">
        <li><svg viewBox="0 0 12 12" aria-hidden="true"><path d="M2.4 0.5l2 2.3-1 1.3c.7 1.5 1.9 2.8 3.5 3.6l1.3-1 2.3 2-1 2.3C5.6 10.6 1.2 6.3.3 2z"/></svg>(555) 014-2290</li>
        <li><svg viewBox="0 0 12 12" aria-hidden="true"><rect x="3" y="0.5" width="6" height="3"/><rect x="0.5" y="4" width="11" height="5" rx="1"/><rect x="3" y="7.5" width="6" height="4" fill="#e3e5e7"/><rect x="3.8" y="8.3" width="4.4" height="2.9"/></svg>(555) 014-2291</li>
        <li><svg viewBox="0 0 12 12" aria-hidden="true"><path d="M0.5 2.5h11v7h-11z M0.5 2.5l5.5 4 5.5-4" stroke="#e3e5e7" stroke-width="0.8"/></svg>info@brellstone-example.com</li>
        <li><svg viewBox="0 0 12 12" aria-hidden="true"><circle cx="6" cy="6" r="5.5"/><path d="M0.5 6h11M6 0.5c-3 3-3 8 0 11M6 0.5c3 3 3 8 0 11M1.5 3.3h9M1.5 8.7h9" stroke="#e3e5e7" stroke-width="0.7" fill="none"/></svg>www.brellstone-example.com</li>
      </ul>
    </div>
  </section>
</main>
</body>
</html>
```